Wordpress Design Project for Employee Communications Site

We need a Wordpress design for a company that strategizes on and produces materials for employee communications. Improving employee communications at all levels of an organization can help improve overall company performance and results. The site needs to look very clean and professional; we're not afraid of white space. We like the functionality that Wordpress provides; however, we only want one "true" blog page; the other pages should give the impression of a more "static" web site - particularly the home page. I have a logo that I can provide.

I have added these comments to the discussion page:
Great question - thank you for asking it. I’ve done more research

I like the very clean and monochromatic looks to many of these. I don’t have to have monochromatic, but I do like minimal colors. Simple, clean, organized. The home page should “fit” almost entirely without scrolling. I do like fat footers that you can scroll down to. I don’t want a colored background, but any that I’ve chosen with colored backgrounds could be switched to a white background.

http://www.mirabelquennet.example/
http://pondraft.example/
http://v1.samplumworth.example/
http://howdythegoat.example/
http://stayingbrisk.example/
http://www.interiors.kelmun.example/
http://trelvmasters.example/

These last two are more corporate sites. The first one is from a well-respected consultant in my area who does a lot of what I do. And I think Harwenby does a nice job with their site. So, I want to marry the look I like with getting the content job done.

http://www.messagefuelbox.example/
http://www.harwenby.example/view/en_US/us/index.htm

Target Market(s)

Target market is mid- to large-sized companies. More than 500 employees.

Industry/Entity Type

Communications

Requirements
Must have
• Need an impactful home page. There should be a "blog" page; contact us; services; about. For starters, at least. I want fonts to be very readable - that is, either quite dark gray or black.
Nice to have
• I am loathe to include a picture of myself, but I do want some images that say, "professional" and "expert" in communications.
Should not have
• I don't want a hits counter :) (I know no one would do that!).

```html
<!DOCTYPE html>
<html lang="en">
<head>
<meta charset="utf-8">
<title>Larkwell Workplace Communications</title>
<link rel="stylesheet" href="https://fonts.googleapis.com/css2?family=Gelasio:wght@400;700&family=Open+Sans:wght@400;600&family=Arimo:wght@400;700&display=swap">
<style>
:root{
  --green:#a5c12e;
  --green-dark:#7f9a1c;
  --green-light:#c6dc4e;
  --blue:#16a9e6;
  --blue-dark:#0b8ccc;
  --ink:#1c1c1c;
  --rule:#cfcfcf;
  --footer:#202020;
  --footer-text:#bdbdbd;
  --footer-muted:#8a8a8a;
  --white:#ffffff;
}
*{box-sizing:border-box;margin:0;padding:0}
html,body{width:813px;height:1200px;overflow:hidden;background:var(--white)}
body{position:relative;font-family:"Gelasio",Georgia,serif;color:var(--ink)}
.abs{position:absolute}

/* header */
.brand{left:60px;top:16px;display:flex;align-items:center;gap:10px}
.brand-mark{width:34px;height:34px;border-radius:50%;background:var(--blue)}
.brand-name{font-family:"Open Sans",sans-serif;font-weight:600;font-size:17px;color:var(--green-dark);line-height:1.15;width:220px}
.search{left:588px;top:13px;width:166px;height:21px;border:1px solid #bbb;border-radius:4px;font-family:"Arimo",sans-serif;font-size:10px;color:#888;padding:4px 8px}
.search svg{position:absolute;right:5px;top:4px}
.nav{left:400px;top:48px;display:flex;gap:2px}
.nav a{display:block;width:88px;height:30px;line-height:32px;text-align:center;white-space:nowrap;color:var(--white);text-decoration:none;font-size:12px;font-weight:700;text-transform:uppercase;border-radius:4px 4px 0 0;background:linear-gradient(var(--blue),var(--blue-dark))}
.nav a.active{background:linear-gradient(var(--green-light),var(--green-dark))}

/* hero */
.hero{left:0;top:77px;width:813px;height:385px;background:linear-gradient(100deg,#2a67b0 0%,#4f8fd0 35%,#8bb9e3 60%,#d8e6f2 100%)}
.hero h1{left:58px;top:78px;font-family:"Open Sans",sans-serif;font-weight:400;font-size:35px;line-height:32px;color:var(--white)}
.hero p{left:61px;top:160px;width:380px;font-size:19px;line-height:24px;color:var(--white);white-space:nowrap}
.btn-read{left:60px;top:274px;width:102px;height:30px;border-radius:5px;background:linear-gradient(var(--green-light),var(--green-dark));color:var(--white);font-size:12.5px;font-weight:700;line-height:30px;padding-left:9px;white-space:nowrap}
.arrow{top:240px;width:27px;height:46px;background:#3a3a3a;display:flex;align-items:center;justify-content:center}
.arrow.prev{left:0;border-radius:0 3px 3px 0}
.arrow.next{right:0;border-radius:3px 0 0 3px}
.pager{left:360px;top:459px;width:85px;height:22px;background:#f2f2f2;border:1px solid #d8d8d8;border-radius:0 0 4px 4px;display:flex;gap:6px;justify-content:center;align-items:center}
.pager i{width:7px;height:7px;border-radius:50%;background:#c8c8c8}
.pager i.on{background:#f0912b}

/* features */
.feature{top:475px;width:180px;text-align:center}
.feature .icon{width:40px;height:42px;margin:0 auto;border-radius:8px}
.feature h3{margin-top:16px;font-size:13.5px;font-weight:700;text-transform:uppercase}
.feature p{margin:9px auto 0;width:152px;font-size:10px;line-height:16.3px}
.divider{top:502px;width:1px;height:148px;background:var(--rule)}

/* boxes */
.box{top:685px;width:194px;height:243px;border:1px solid var(--rule)}
.box h2{height:32px;background:linear-gradient(var(--green-light),var(--green-dark));color:var(--white);font-size:13px;font-weight:400;line-height:32px;padding-left:16px;text-transform:uppercase}
.box .copy{padding:14px 12px 0 17px;font-size:8.1px;line-height:12.2px}
.box .copy p+p{margin-top:12px}
.box ul{list-style:none;padding:12px 8px 0 30px;font-size:8.1px;line-height:20.3px;white-space:nowrap}
.btn-more{right:13px;bottom:13px;width:47px;height:22px;border-radius:6px;background:linear-gradient(#3cc3f5,var(--blue-dark));color:var(--white);font-size:10.5px;text-align:center;line-height:22px}

/* footer */
.footer{left:0;top:953px;width:813px;height:247px;background:var(--footer)}
.col{top:22px;width:146px}
.col h4{font-size:13.5px;font-weight:400;color:var(--white);text-transform:uppercase;padding-bottom:8px;border-bottom:1px solid #3a3a3a}
.links{list-style:none;margin-top:12px;font-family:"Arimo",sans-serif;font-size:9.5px;color:var(--footer-text)}
.links li{height:22.5px;padding-left:14px;position:relative}
.links li::before{content:"›";position:absolute;left:0;top:-2px;font-size:11px}
.post{display:flex;gap:9px;margin-top:13px;font-family:"Arimo",sans-serif}
.post .thumb{width:40px;height:38px;border:2px solid #444;flex:none}
.post b{display:block;font-weight:400;font-size:9px;color:var(--footer-text)}
.post span{display:block;font-size:7.5px;line-height:11px;color:var(--footer-muted);margin-top:3px}
.social{list-style:none;margin-top:14px;font-family:"Arimo",sans-serif;font-size:8.3px;color:var(--footer-muted)}
.social li{display:flex;align-items:center;gap:10px;height:22.5px}
.social i{width:17px;height:17px;border-radius:50%;background:#2d86c4}
.social i.rss{background:#e8772a}
.field{height:19px;background:#161616;border:1px solid #333;margin-top:5px;font-family:"Arimo",sans-serif;font-size:7px;color:var(--footer-text);padding:5px 7px}
.field.area{height:56px}
.submit{width:42px;height:19px;margin-top:5px;background:#161616;border:1px solid #333;font-family:"Arimo",sans-serif;font-size:7px;color:var(--footer-text);text-align:center;line-height:17px}
.copyright{left:58px;top:1152px;width:696px;height:38px;background:var(--green-light);border-radius:4px;font-family:"Arimo",sans-serif;font-size:6.5px;text-align:center;line-height:38px;color:#333}
</style>
</head>
<body>

<header>
  <div class="abs brand"><span class="brand-mark"></span><span class="brand-name">Larkwell Workplace Communications</span></div>
  <div class="abs search">Search
    <svg width="10" height="10" viewBox="0 0 10 10"><circle cx="6" cy="4" r="3" fill="none" stroke="#2a78b5" stroke-width="1.4"/><line x1="4" y1="6" x2="1" y2="9" stroke="#2a78b5" stroke-width="1.6"/></svg>
  </div>
  <nav class="abs nav">
    <a class="active" href="#">About Us</a><a href="#">Services</a><a href="#">Blog</a><a href="#">Contact Us</a>
  </nav>
</header>

<section class="abs hero" role="img" aria-label="Businesswoman talking on a mobile phone in front of a glass office tower reflecting blue sky">
  <h1 class="abs">Create your own<br>business network</h1>
  <p class="abs">We are ready to offer you our best and<br>latest results of research because high<br>technologies are our mission,<br>and we are glad to help you in this.</p>
  <div class="abs btn-read">READ MORE ▸</div>
  <div class="abs arrow prev"><svg width="8" height="12"><path d="M7 1 2 6l5 5" fill="none" stroke="#fff" stroke-width="2"/></svg></div>
  <div class="abs arrow next"><svg width="8" height="12"><path d="M1 1l5 5-5 5" fill="none" stroke="#fff" stroke-width="2"/></svg></div>
</section>
<div class="abs pager"><i class="on"></i><i></i><i></i><i></i><i></i></div>

<section class="features">
  <div class="abs feature" style="left:69px"><div class="icon" role="img" aria-label="Gift bag icon" style="background:linear-gradient(#f39a3a,#d2462a)"></div><h3>Variety</h3><p>Uis ultricies pharra one san maesda ot am rosr sit ameon etudipiscing elit. Mauris ferme. ultricies pharra one san maesda ot am rosr sit ameon etudipiscing elit. Mauris ferme.</p></div>
  <div class="abs divider" style="left:227px"></div>
  <div class="abs feature" style="left:224px"><div class="icon" role="img" aria-label="Mobile phone icon" style="background:linear-gradient(#b67ee0,#6d3aa8)"></div><h3>Speed</h3><p>Uis ultricies pharra one san maesda ot am rosr sit ameon etudipiscing elit. Mauris ferme. ultricies pharra one san maesda ot am rosr sit ameon etudipiscing elit. Mauris ferme.</p></div>
  <div class="abs divider" style="left:403px"></div>
  <div class="abs feature" style="left:406px"><div class="icon" role="img" aria-label="Hot air balloon icon" style="background:linear-gradient(#f25a4a,#b81e1e)"></div><h3>Quality</h3><p>Uis ultricies pharra one san maesda ot am rosr sit ameon etudipiscing elit. Mauris ferme. ultricies pharra one san maesda ot am rosr sit ameon etudipiscing elit. Mauris ferme.</p></div>
  <div class="abs divider" style="left:586px"></div>
  <div class="abs feature" style="left:581px"><div class="icon" role="img" aria-label="Speech bubbles icon" style="background:linear-gradient(#f5b33a,#3a9ee0)"></div><h3>Customers</h3><p>Uis ultricies pharra one san maesda ot am rosr sit ameon etudipiscing elit. Mauris ferme. ultricies pharra one san maesda ot am rosr sit ameon etudipiscing elit. Mauris ferme.</p></div>
</section>

<section>
  <article class="abs box" style="left:58px">
    <h2>Welcome</h2>
    <div class="copy">
      <p>Solunbis esmqedit quo ms tristique o em uis ultricies pharra one san maesda ot amet. erosr sit ameonsecetuer adipiscing eliis ferm entum dictum magned t aliquam leo.</p>
      <p>Solunbis esmqedit quo ms tristique o em uis ultricies pharra one san maesda ot amet. erosr sit ameonsecetuer adipiscing eliis ferm entum dictum magned t aliquam leo. erosr sit ameonsecetuer adipiscing eliis ferm entum dictum magned t aliquam leo.</p>
    </div>
    <div class="abs btn-more">MORE</div>
  </article>
  <article class="abs box" style="left:305px">
    <h2>Services</h2>
    <ul>
      <li>Solunbis esmqedit quistique</li><li>Pharra one san maein faucibsda ot ame</li><li>Ut telluin faucibs dolor dapibus eget</li><li>Aenean auctor wisi et uin faucibrna</li><li>Eliquam erat volutin faucibpat</li><li>Duin faucibis ac turpieger rutrum ante</li><li>Vestibulum libero nis porta veele</li><li>Etiam cursus lein faucibel metus</li>
    </ul>
    <div class="abs btn-more">MORE</div>
  </article>
  <article class="abs box" style="left:560px">
    <h2>News &amp; Events</h2>
    <div class="copy">
      <p>Solunbis esmqedit quo ms tristique o em uis ultricies pharra one san maesda ot amet. erosr sit ameonsecetuer adipiscing eliis ferm entum dictum magned t aliquam leo.</p>
      <p>Solunbis esmqedit quo ms tristique o em uis ultricies pharra one san maesda ot amet. erosr sit ameonsecetuer adipiscing eliis ferm entum dictum magned t aliquam leo. erosr sit ameonsecetuer adipiscing eliis ferm entum dictum magned t aliquam leo.</p>
    </div>
    <div class="abs btn-more">MORE</div>
  </article>
</section>

<footer class="abs footer">
  <div class="abs col" style="left:62px">
    <h4>Useful Resources</h4>
    <ul class="links"><li>Lorem ipsum Dolor Sit Amet</li><li>Lorem ipsum Dolor Sit Amet</li><li>Lorem ipsum Dolor Sit Amet</li><li>Lorem ipsum Dolor Sit Amet</li><li>Lorem ipsum Dolor Sit Amet</li></ul>
  </div>
  <div class="abs col" style="left:231px">
    <h4>Blog Posts</h4>
    <div class="post"><div class="thumb" role="img" aria-label="Blog post thumbnail, sunset scene" style="background:linear-gradient(#e7a24a,#b65a22)"></div><div><b>Lorem Ipsum is simply</b><span>The printing and typesetting industry has been industry...</span></div></div>
    <div class="post"><div class="thumb" role="img" aria-label="Blog post thumbnail, ball on grass" style="background:linear-gradient(#5a9fe0,#4c9a2a)"></div><div><b>Lorem Ipsum is simply</b><span>The printing and typesetting industry has been industry...</span></div></div>
  </div>
  <div class="abs col" style="left:399px">
    <h4>Get Social</h4>
    <ul class="social"><li><i></i>Follow us on Tweetlane</li><li><i></i>Friendship on Friendspace</li><li><i></i>Visit us on Worklinkr</li><li><i></i>See our Vids on Clipvault</li><li><i class="rss"></i>Subscribe to RSS Feed</li></ul>
  </div>
  <div class="abs col" style="left:566px;width:147px">
    <h4>Contact Us</h4>
    <div class="field" style="margin-top:12px">Name</div>
    <div class="field">Email</div>
    <div class="field area"></div>
    <div class="submit">Submit</div>
  </div>
</footer>
<div class="abs copyright">© COPYRIGHTS 2012. ALL RIGHTS RESERVED.</div>

</body>
</html>
```